I need a flyer made , the flyer can be one page or two pages or three pages . I will be posting this on Instagram and social media platforms. I am a luxury home builder , I am looking to hire a construction project manager . Below are some examples and ideas what can be on the flyer

We’re looking for a construction project manager who’s passionate about building luxury homes at the highest standards
We’re hiring construction project manager
* Experience 5+ years in residential project management with a strong portfolio of completed homes.
* location : Bergen County NJ
* excellent leadership skills, leads teams with confidence and clarity
* communicates seamlessly with architects , engineers, designers and clients
*knows how to manage budgets and timelines without compromising quality
*solves problems with a positive solution first mindset
* pays attention to every detail because in luxury the small things are the big things

Apply now , link in bio or DM to connect.

My logo is attached, my web site www.velstridebuilders.com
My style is modern but still warm and inviting. I like a clean classy look .

Please don’t add any images of chairs or people to the flyer , I do not want people on my flyer. Do not add standard images of offices and houses , we are luxury builders , we build homes over 2 million dollars. Keep a classy , simple modern look . High end .

You can add a white hard hat with my logo on it for a image , this is a suggestion does not have to be on my flyer ,

```html
<!DOCTYPE html>
<html lang="en">
<head>
<meta charset="utf-8">
<title>Velstride Builders – We're Hiring</title>
<link href="https://fonts.googleapis.com/css2?family=Poppins:wght@200;300;400;500;600;700;800&display=swap" rel="stylesheet">
<style>
  :root {
    --page: #cfd3d9;
    --paper: #eef0f1;
    --ink: #0e0e0e;
    --ink-soft: #2a2a2a;
    --rule: #a7abb1;
    --band-grey: #d4d8de;
    --band-black: #0b0b0b;
    --white: #ffffff;
  }
  * { margin: 0; padding: 0; box-sizing: border-box; }
  html, body {
    width: 1200px;
    height: 655px;
    overflow: hidden;
    background: var(--page);
    font-family: "Poppins", sans-serif;
    color: var(--ink);
  }
  .flyer {
    position: absolute;
    left: 0;
    top: 13px;
    width: 1200px;
    height: 628px;
    overflow: hidden;
    background: var(--paper);
  }
  .flyer__art {
    position: absolute;
    inset: 0;
    width: 1200px;
    height: 628px;
  }
  .brand {
    position: absolute;
    top: 30px;
    font-size: 25px;
    font-weight: 500;
    letter-spacing: 0.08em;
    line-height: 1.18;
    text-transform: uppercase;
    color: var(--ink);
  }
  .brand--left { left: 28px; text-align: left; }
  .brand--right { right: 26px; text-align: right; }

  .headline {
    position: absolute;
    right: 758px;
    top: 142px;
    text-align: right;
    line-height: 0.9;
  }
  .headline__light {
    display: block;
    padding-right: 38px;
    font-size: 80px;
    font-weight: 200;
    letter-spacing: -0.03em;
  }
  .headline__bold {
    display: block;
    font-size: 79px;
    font-weight: 700;
    letter-spacing: -0.02em;
  }

  .intro {
    position: absolute;
    right: 27px;
    top: 138px;
    width: 330px;
    text-align: right;
    font-size: 15px;
    font-weight: 700;
    line-height: 19.2px;
  }
  .role {
    position: absolute;
    right: 28px;
    top: 258px;
    text-align: right;
  }
  .role__kicker {
    display: block;
    font-size: 36px;
    font-weight: 200;
    line-height: 38px;
    letter-spacing: -0.02em;
  }
  .role__title {
    display: block;
    font-size: 35px;
    font-weight: 700;
    line-height: 31px;
    letter-spacing: -0.01em;
  }
  .role__rule {
    position: absolute;
    left: 833px;
    top: 372px;
    width: 339px;
    height: 4px;
    background: var(--rule);
  }
  .requirements {
    position: absolute;
    left: 668px;
    top: 385px;
    list-style: none;
  }
  .requirements li {
    position: relative;
    padding-left: 11px;
    font-size: 9.95px;
    font-weight: 400;
    line-height: 23.3px;
    color: var(--ink-soft);
    white-space: nowrap;
  }
  .requirements li::before {
    content: "";
    position: absolute;
    left: 0;
    top: 9px;
    width: 5px;
    height: 5px;
    background: var(--rule);
  }
  .cta {
    position: absolute;
    left: 668px;
    top: 572px;
    font-size: 13px;
    line-height: 14px;
    color: var(--ink);
  }
  .cta__strong { display: block; font-weight: 600; }
  .cta__sub { display: block; font-weight: 400; }
  .site {
    position: absolute;
    top: 580px;
    font-size: 9.5px;
    font-weight: 300;
    color: var(--white);
  }
  .site--left { left: 27px; }
  .site--right { right: 28px; }
</style>
</head>
<body>
<main class="flyer">
  <svg class="flyer__art" viewBox="0 0 1200 628" xmlns="http://www.w3.org/2000/svg">
    <defs>
      <linearGradient id="hillside-wash" x1="0" y1="0" x2="0" y2="1">
        <stop offset="0" stop-color="#f1f3f4"/>
        <stop offset="0.45" stop-color="#e4e8e5"/>
        <stop offset="1" stop-color="#dce1dc"/>
      </linearGradient>
      <linearGradient id="villa-wash" x1="0" y1="0" x2="1" y2="0">
        <stop offset="0" stop-color="#e6e9ea"/>
        <stop offset="1" stop-color="#eef0f1"/>
      </linearGradient>
      <radialGradient id="sketch-wash" cx="0.45" cy="0.55" r="0.55">
        <stop offset="0" stop-color="#cfd3d1" stop-opacity="0.9"/>
        <stop offset="0.6" stop-color="#d6dad8" stop-opacity="0.55"/>
        <stop offset="1" stop-color="#dde1de" stop-opacity="0"/>
      </radialGradient>
      <linearGradient id="villa-dusk" x1="0" y1="0" x2="0" y2="1">
        <stop offset="0" stop-color="#34502e"/>
        <stop offset="0.22" stop-color="#5f6b74"/>
        <stop offset="0.45" stop-color="#7c8196"/>
        <stop offset="0.75" stop-color="#6f7689"/>
        <stop offset="1" stop-color="#2c4229"/>
      </linearGradient>
      <radialGradient id="villa-glow" cx="0.5" cy="0.5" r="0.5">
        <stop offset="0" stop-color="#d9a860" stop-opacity="0.85"/>
        <stop offset="1" stop-color="#d9a860" stop-opacity="0"/>
      </radialGradient>
      <radialGradient id="pool-glow" cx="0.5" cy="0.5" r="0.5">
        <stop offset="0" stop-color="#2a9bb5" stop-opacity="0.9"/>
        <stop offset="1" stop-color="#2a9bb5" stop-opacity="0"/>
      </radialGradient>
      <clipPath id="photo-band">
        <polygon points="690,0 993,0 462,628 153,628"/>
      </clipPath>
    </defs>

    <rect role="img" aria-label="Faded hillside view behind a modern villa" x="0" y="0" width="700" height="628" fill="url(#hillside-wash)"/>
    <rect role="img" aria-label="Faded terraces of a modern luxury villa" x="700" y="0" width="500" height="628" fill="url(#villa-wash)"/>
    <ellipse role="img" aria-label="Soft line drawing of a modern home with a terrace" cx="170" cy="430" rx="230" ry="130" fill="url(#sketch-wash)"/>

    <polygon points="680,0 1003,0 472,628 143,628" fill="#f6f7f8"/>
    <g role="img" aria-label="Photograph of a multi-level luxury villa with an infinity pool at dusk" clip-path="url(#photo-band)">
      <rect x="150" y="0" width="850" height="628" fill="url(#villa-dusk)"/>
      <ellipse cx="640" cy="270" rx="190" ry="90" fill="url(#villa-glow)"/>
      <ellipse cx="500" cy="390" rx="150" ry="70" fill="url(#villa-glow)" opacity="0.7"/>
      <ellipse cx="440" cy="420" rx="130" ry="60" fill="url(#pool-glow)"/>
    </g>

    <polygon points="0,567 196,567 162,607 0,607" fill="var(--band-black)"/>
    <polygon points="512,567 998,567 964,607 478,607" fill="var(--band-grey)"/>
    <polygon points="1001,567 1200,567 1200,607 967,607" fill="var(--band-black)"/>
  </svg>

  <div class="brand brand--left">Velstride<br>Builders</div>
  <div class="brand brand--right">Velstride<br>Builders</div>

  <h1 class="headline">
    <span class="headline__light">WE’RE</span>
    <span class="headline__bold">HIRING</span>
  </h1>

  <p class="intro">We’re looking for a construction<br>project manager who’s passionate<br>about building luxury homes at the<br>highest standards</p>

  <h2 class="role">
    <span class="role__kicker">WE’RE HIRING</span>
    <span class="role__title">CONSTRUCTION</span>
    <span class="role__title">PROJECT MANAGER</span>
  </h2>
  <div class="role__rule"></div>

  <ul class="requirements">
    <li>Experience 5+ years in residential project management with a strong portfolio of completed homes</li>
    <li>Location : Bergen County NJ</li>
    <li>Excellent leadership skills, leads teams with confidence and clarity</li>
    <li>Communicates seamlessly with architects, engineers, designers and clients</li>
    <li>Knows how to manage budgets and timelines without compromising quality</li>
    <li>Solves problems with a positive solution first mindset</li>
    <li>Pays attention to every detail because in luxury the small things are the big things</li>
  </ul>

  <p class="cta">
    <span class="cta__strong">APPLY NOW,</span>
    <span class="cta__sub">LINK IN BIO OR DM TO CONNECT</span>
  </p>

  <span class="site site--left">www.velstridebuilders.com</span>
  <span class="site site--right">www.velstridebuilders.com</span>
</main>
</body>
</html>
```